Standard Company Posters / Notices

We have manufacturing sites, across the sites there are notices that managers put up, sometimes like a poster or door notice. These are not in any standard format or follow any standard layout. We wanted to create a notice template that could be adopted with layout guidance for all our internal notices. Some examples of the notices are below. We have three different sites so we would want to interchange the logo to suit the location, I have also added some images used for our values awards as examples of the look we like.

Target Market(s)

Employees

Industry/Entity Type

Food Manufacturing

Requirements
Must have
• Flexible for the site teams to amend to suit their needs.

```html
<!DOCTYPE html>
<html lang="en">
<head>
<meta charset="utf-8">
<title>Site Notice – Mobile Phones Prohibited</title>
<link rel="stylesheet" href="https://fonts.googleapis.com/css2?family=Outfit:wght@400;500;600;700;800&display=swap">
<style>
  :root {
    --brand-red: #b90e20;
    --ink: #050505;
    --paper: #ffffff;
    --mark-grey: #ececec;
    --mark-text: #dcdcdc;
  }
  * { box-sizing: border-box; margin: 0; padding: 0; }
  html, body { width: 849px; height: 1200px; overflow: hidden; background: var(--paper); }
  body { font-family: "Outfit", sans-serif; color: var(--ink); }

  .notice { position: relative; width: 849px; height: 1200px; background: var(--paper); overflow: hidden; }

  /* Header */
  .notice-header { position: absolute; left: 0; top: 0; width: 849px; height: 240px; }
  .header-band {
    position: absolute; left: 226px; top: 65px; width: 544px; height: 151px;
    background: var(--brand-red); color: var(--paper); text-align: center;
    padding-left: 90px;
  }
  .header-title { font-weight: 800; font-size: 64px; line-height: 1; margin-top: 27px; letter-spacing: 0.5px; }
  .header-subtitle { font-weight: 700; font-size: 44px; line-height: 1; margin-top: 4px; }
  .warning-icon { position: absolute; left: 76px; top: 30px; width: 240px; height: 206px; }

  /* Faint site mark */
  .site-mark {
    position: absolute; left: 268px; top: 302px; width: 290px; height: 470px;
    background: var(--mark-grey); opacity: 0.7;
  }
  .site-mark-name {
    position: absolute; left: 95px; width: 660px; top: 500px; text-align: center;
    font-weight: 800; font-size: 74px; color: var(--mark-text); opacity: 0.7; line-height: 1;
  }

  /* Message */
  .message { position: absolute; left: 0; top: 0; width: 849px; text-align: center; }
  .message-line { position: absolute; left: 0; width: 849px; line-height: 1; font-weight: 700; white-space: nowrap; }
  .line-normal { font-size: 59px; }
  .line-emphasis { font-size: 111px; font-weight: 700; color: var(--brand-red); letter-spacing: -1px; }

  /* Footer */
  .footer-frame {
    position: absolute; left: 66px; top: 985px; width: 717px; height: 176px;
    border: 4px solid var(--brand-red); border-radius: 12px;
  }
  .footer-label {
    position: absolute; left: 138px; top: 948px; width: 573px; height: 66px;
    background: var(--paper); padding: 0 4px;
  }
  .footer-label span {
    display: block; height: 100%; background: var(--brand-red); border-radius: 8px;
    color: var(--paper); font-weight: 700; font-size: 40px; line-height: 66px; text-align: center;
  }
  .contact-row {
    position: absolute; left: 106px; top: 1032px; width: 640px;
    display: flex; justify-content: space-between; align-items: center;
    font-weight: 600; font-size: 27px; line-height: 1;
  }
  .contact-item { display: flex; align-items: center; gap: 4px; }
  .contact-item svg { width: 24px; height: 24px; }
  .address { position: absolute; left: 106px; width: 640px; top: 1075px; font-size: 25.5px; line-height: 34px; font-weight: 500; }
  .address-line { display: flex; align-items: center; gap: 4px; }
  .address-line svg { width: 20px; height: 22px; }
  .address-line.indent { padding-left: 78px; }
</style>
</head>
<body>
<main class="notice">

  <header class="notice-header">
    <div class="header-band">
      <div class="header-title">ATTENTION</div>
      <div class="header-subtitle">PLEASE!</div>
    </div>
    <svg class="warning-icon" viewBox="0 0 240 206" aria-hidden="true">
      <path d="M114 8 Q120 -2 126 8 L232 190 Q238 204 222 204 L18 204 Q2 204 8 190 Z" fill="#b90e20" stroke="#ffffff" stroke-width="8" stroke-linejoin="round"/>
      <path d="M103 72 Q103 64 114 64 Q125 64 125 72 L120 134 Q119 140 114 140 Q109 140 108 134 Z" fill="#ffffff"/>
      <circle cx="114" cy="160" r="12" fill="#ffffff"/>
    </svg>
  </header>

  <div class="site-mark" aria-hidden="true"></div>
  <div class="site-mark-name" aria-hidden="true">HARTWELL DAIRY</div>

  <section class="message">
    <p class="message-line line-normal" style="top:334px">MOBILE PHONES ARE</p>
    <p class="message-line line-emphasis" style="top:405px">PROHIBITED</p>
    <p class="message-line line-normal" style="top:512px">IN THIS AREA</p>
    <p class="message-line line-normal" style="top:574px">UNLESS YOU ARE</p>
    <p class="message-line line-emphasis" style="top:636px">AUTHORISED</p>
    <p class="message-line line-normal" style="top:744px">AND ON THE</p>
    <p class="message-line line-normal" style="top:806px">CONCESSION LIST!</p>
  </section>

  <footer>
    <div class="footer-frame"></div>
    <div class="footer-label"><span>SIGNED BY: MANAGEMENT</span></div>

    <div class="contact-row">
      <span class="contact-item">
        <svg viewBox="0 0 24 24" aria-hidden="true">
          <circle cx="12" cy="12" r="10.5" fill="none" stroke="#050505" stroke-width="1.6"/>
          <path d="M8 6.5 L10 6 L11.2 9 L9.8 10.2 Q11 13 13.8 14.2 L15 12.8 L18 14 L17.5 16 Q16.5 17.5 14.5 17 Q8.5 15 7 9.5 Q6.6 7.5 8 6.5 Z" fill="#050505"/>
        </svg>+44 1632 960500
      </span>
      <span class="contact-item">
        <svg viewBox="0 0 24 24" aria-hidden="true">
          <g fill="none" stroke="#050505" stroke-width="1.6">
            <circle cx="12" cy="12" r="9"/>
            <ellipse cx="12" cy="12" rx="4" ry="9"/>
            <line x1="3" y1="12" x2="21" y2="12"/>
            <line x1="12" y1="3" x2="12" y2="21"/>
          </g>
        </svg>www.hartwell-dairy.co.uk
      </span>
    </div>

    <address class="address" style="font-style:normal">
      <div class="address-line">
        <svg viewBox="0 0 20 22" aria-hidden="true">
          <path d="M10 1 Q18 1 18 9 Q18 14 10 21 Q2 14 2 9 Q2 1 10 1 Z" fill="#050505"/>
          <circle cx="10" cy="9" r="3.2" fill="#ffffff"/>
        </svg>Elm Tree Farm, Ashbury, Westmoor, Cheshire
      </div>
      <div class="address-line indent">AB1 2CD , Westmoor, United Kingdom</div>
    </address>
  </footer>

</main>
</body>
</html>
```